Looking for a cool, modern Cannabis Jar Label

I want you to come up with a better, modern look for a label.

I need it sized to 4” x 3” - I plan to print directly to label printer.

I want you to use Photoshop and deliver me a layered PSD file that I can edit and modify the information as needed..

The label information will need to include places for:
(1) Strain Name - most important part of label - larger font size than rest - example Kestrel Mist, PLV #7, Juniper Hollow
(2) Pricing - for Gram, 1/8, 1/4, 1/2. and Ounce
(3) Strain Designation (Hybrid, Indica or Sativa) - maybe color coded, different color for Indica v. Sativa, just an idea
(4) THC and CBD percentages - for example 23% THC and 0.05% CBD
(5) Farm name - a place where we can add the name/logo of the business that produced the product. example - Ovenrow Farms

I have attached a simple mockup showing the information.

I have also attached a few samples of labels we like to give you an idea of the look and feel we are going for.

I am wanting a very clean, modern, classy, readable look.The font will use is Gotham Font.

HI Everyone! Thank you for all of your designs. I am requesting an extension because I need more time to give adequate feedback to the designers. Thank you for your participation and all of your efforts! I will be making a decision soon!

• Gotham Font

• Thank you for your designs. I am sorry i have been slow in providing feedback, things have been really busy around here!
• I wanted to give some group general feedback. After reviewing all of the designs, there is a common theme among all of the designs that I would like to see changed.
• I would like to see the per gram pricing more prominent on the label. This is what most people are looking for when they are purchasing the product. So I would like to see this stand out from the other pricing tiers. As I think about it, they don't all need to be grouped together in a line. You could have the Per Gram pricing front and center some where and then the other pricing tiers grouped together somewhere else on the label.
• This is the order of importance of items on the label. Items at the the top of the list should be bigger than those below it.
• 1. Strain name
• 2. Pricing - being per gram the most important of all prices
• 3. THC/CBD percentages
• 4. Strain Type (indica, sativa, hybrid)
• 5. Farm name/logo
• When laying out these labels, they will be going on rounded jars and they will be on display. Think of jars with fancy labels in a candy store. They need to be eye catchy, appealing, but easy read.
• Thank you for all of your hard work, everyone is doing a great job.
• Best,
• Neta

```html
<!DOCTYPE html>
<html lang="en">
<head>
<meta charset="utf-8">
<title>Strain Jar Labels – Hybrid, Sativa, Indica</title>
<link href="https://fonts.googleapis.com/css2?family=Montserrat:wght@300;400;500;600;700;800;900&display=swap" rel="stylesheet">
<style>
  :root {
    --ink: #111111;
    --paper: #ffffff;
    --shadow: #c9c9c9;
    --hybrid: #3d53a6;
    --sativa: #ee2226;
    --indica: #00a651;
    --font: "Montserrat", Arial, sans-serif;
  }
  html, body {
    margin: 0;
    padding: 0;
    width: 1200px;
    height: 1200px;
    overflow: hidden;
    background: var(--paper);
    font-family: var(--font);
    color: var(--ink);
  }
  .sheet { position: relative; width: 1200px; height: 1200px; }

  .label {
    position: absolute;
    width: 509px;
    height: 381px;
    background: var(--paper);
    box-shadow: 10px 8px 0 var(--shadow), 0 10px 40px rgba(0,0,0,0.06);
  }
  .label--hybrid { left: 56px;  top: 184px; --type: var(--hybrid); }
  .label--sativa { left: 636px; top: 184px; --type: var(--sativa); }
  .label--indica { left: 369px; top: 635px; --type: var(--indica); }

  .strain-name {
    position: absolute;
    left: 0; top: 20px;
    width: 402px;
    margin: 0;
    text-align: center;
    white-space: nowrap;
    font-size: 46px;
    font-weight: 800;
    line-height: 44px;
    letter-spacing: 0.3px;
    text-transform: uppercase;
  }
  .title-divider {
    position: absolute;
    left: 402px; top: 12px;
    width: 2px; height: 104px;
    background: var(--ink);
  }
  .farm {
    position: absolute;
    left: 411px; top: 50px;
    display: flex;
    align-items: center;
    gap: 5px;
  }
  .farm-dot {
    width: 26px; height: 26px;
    border: 2px solid var(--ink);
    border-radius: 50%;
    box-sizing: border-box;
    flex: none;
  }
  .farm-name {
    font-size: 10px;
    font-weight: 800;
    line-height: 11px;
    letter-spacing: 0.3px;
    text-transform: uppercase;
  }

  .rule {
    position: absolute;
    left: 0; width: 509px; height: 7px;
    background: var(--ink);
  }
  .rule--top { top: 127px; }
  .rule--bottom { top: 282px; }

  .prices {
    position: absolute;
    left: 0; top: 148px;
    width: 509px; height: 122px;
    display: flex;
  }
  .tier {
    position: relative;
    flex: 1;
    text-align: center;
  }
  .tier + .tier { border-left: 1px solid var(--ink); }
  .tier-name {
    display: block;
    margin-top: 4px;
    font-size: 17px;
    font-weight: 400;
    letter-spacing: 1px;
  }
  .tier-price {
    position: absolute;
    left: 0; right: 0; bottom: 26px;
    white-space: nowrap;
    font-size: 39px;
    font-weight: 500;
    letter-spacing: -1px;
    line-height: 1;
  }
  .tier-price .currency {
    font-size: 18px;
    font-weight: 700;
    letter-spacing: 0;
    margin-right: 2px;
  }
  .tier--gram .tier-price {
    font-size: 68px;
    font-weight: 600;
    letter-spacing: -3px;
    bottom: 22px;
  }

  .stats {
    position: absolute;
    left: 0; top: 289px;
    width: 509px; height: 92px;
  }
  .stats svg { position: absolute; left: 0; top: 0; }
  .strain-type {
    position: absolute;
    left: 0; top: 26px;
    width: 150px;
    text-align: center;
    font-size: 31px;
    font-weight: 900;
    color: var(--paper);
    text-transform: uppercase;
    letter-spacing: -0.5px;
    line-height: 36px;
  }
  .stat {
    position: absolute;
    top: 0;
    width: 170px;
    text-align: center;
  }
  .stat--thc { left: 171px; }
  .stat--cbd { left: 331px; }
  .stat-label {
    display: block;
    font-size: 29px;
    font-weight: 300;
    letter-spacing: 8px;
    line-height: 32px;
    padding-left: 8px;
  }
  .stat-value {
    display: block;
    white-space: nowrap;
    font-size: 46px;
    font-weight: 900;
    letter-spacing: -3px;
    line-height: 48px;
    color: var(--type);
  }
</style>
</head>
<body>
<main class="sheet">

  <article class="label label--hybrid">
    <h1 class="strain-name">Copper Ridge<br>Shiver</h1>
    <div class="title-divider"></div>
    <div class="farm"><span class="farm-dot"></span><span class="farm-name">Ovenrow<br>Farms</span></div>
    <div class="rule rule--top"></div>
    <div class="prices">
      <div class="tier"><span class="tier-name">eight</span><div class="tier-price"><span class="currency">$</span>35</div></div>
      <div class="tier"><span class="tier-name">quarter</span><div class="tier-price"><span class="currency">$</span>70</div></div>
      <div class="tier tier--gram"><span class="tier-name">gram</span><div class="tier-price"><span class="currency">$</span>10</div></div>
      <div class="tier"><span class="tier-name">half</span><div class="tier-price"><span class="currency">$</span>140</div></div>
      <div class="tier"><span class="tier-name">ounce</span><div class="tier-price"><span class="currency">$</span>280</div></div>
    </div>
    <div class="rule rule--bottom"></div>
    <div class="stats">
      <svg width="509" height="92" viewBox="0 0 509 92">
        <polygon points="0,0 164,0 148,92 0,92" fill="var(--hybrid)"/>
        <polygon points="164,0 173,0 157,92 148,92" fill="var(--ink)"/>
        <polygon points="341,0 349,0 330,92 322,92" fill="var(--ink)"/>
      </svg>
      <div class="strain-type">Hybrid</div>
      <div class="stat stat--thc"><span class="stat-label">THC</span><span class="stat-value">23%</span></div>
      <div class="stat stat--cbd"><span class="stat-label">CBD</span><span class="stat-value">0.05%</span></div>
    </div>
  </article>

  <article class="label label--sativa">
    <h1 class="strain-name">Copper Ridge<br>Shiver</h1>
    <div class="title-divider"></div>
    <div class="farm"><span class="farm-dot"></span><span class="farm-name">Ovenrow<br>Farms</span></div>
    <div class="rule rule--top"></div>
    <div class="prices">
      <div class="tier"><span class="tier-name">eight</span><div class="tier-price"><span class="currency">$</span>35</div></div>
      <div class="tier"><span class="tier-name">quarter</span><div class="tier-price"><span class="currency">$</span>70</div></div>
      <div class="tier tier--gram"><span class="tier-name">gram</span><div class="tier-price"><span class="currency">$</span>10</div></div>
      <div class="tier"><span class="tier-name">half</span><div class="tier-price"><span class="currency">$</span>140</div></div>
      <div class="tier"><span class="tier-name">ounce</span><div class="tier-price"><span class="currency">$</span>280</div></div>
    </div>
    <div class="rule rule--bottom"></div>
    <div class="stats">
      <svg width="509" height="92" viewBox="0 0 509 92">
        <polygon points="0,0 164,0 148,92 0,92" fill="var(--sativa)"/>
        <polygon points="164,0 173,0 157,92 148,92" fill="var(--ink)"/>
        <polygon points="341,0 349,0 330,92 322,92" fill="var(--ink)"/>
      </svg>
      <div class="strain-type">Sativa</div>
      <div class="stat stat--thc"><span class="stat-label">THC</span><span class="stat-value">23%</span></div>
      <div class="stat stat--cbd"><span class="stat-label">CBD</span><span class="stat-value">0.05%</span></div>
    </div>
  </article>

  <article class="label label--indica">
    <h1 class="strain-name">Copper Ridge<br>Shiver</h1>
    <div class="title-divider"></div>
    <div class="farm"><span class="farm-dot"></span><span class="farm-name">Ovenrow<br>Farms</span></div>
    <div class="rule rule--top"></div>
    <div class="prices">
      <div class="tier"><span class="tier-name">eight</span><div class="tier-price"><span class="currency">$</span>35</div></div>
      <div class="tier"><span class="tier-name">quarter</span><div class="tier-price"><span class="currency">$</span>70</div></div>
      <div class="tier tier--gram"><span class="tier-name">gram</span><div class="tier-price"><span class="currency">$</span>10</div></div>
      <div class="tier"><span class="tier-name">half</span><div class="tier-price"><span class="currency">$</span>140</div></div>
      <div class="tier"><span class="tier-name">ounce</span><div class="tier-price"><span class="currency">$</span>280</div></div>
    </div>
    <div class="rule rule--bottom"></div>
    <div class="stats">
      <svg width="509" height="92" viewBox="0 0 509 92">
        <polygon points="0,0 164,0 148,92 0,92" fill="var(--indica)"/>
        <polygon points="164,0 173,0 157,92 148,92" fill="var(--ink)"/>
        <polygon points="341,0 349,0 330,92 322,92" fill="var(--ink)"/>
      </svg>
      <div class="strain-type">Indica</div>
      <div class="stat stat--thc"><span class="stat-label">THC</span><span class="stat-value">23%</span></div>
      <div class="stat stat--cbd"><span class="stat-label">CBD</span><span class="stat-value">0.05%</span></div>
    </div>
  </article>

</main>
</body>
</html>
```